Construction material supplies company business card ****

1. Full company name “K T Masonry Works Ltd”
I am after a Business card design for the company as a whole. We are better known in Solomon Islands as “K T Masonry” for short.

We are a building materials supplier of
Ready Mixed Concrete, Bricks and Blocks,
Quarry products- gravel, aggregates, sand etc.
Cement distributor/retailer of reputable brands.
Other prefab concrete products. Culverts, wave breakers, concrete retaining blocks etc.

2. Competitive Advantage over Competition: Quality, efficient, professional, dependable, reliable

3. We want people to feel trust worthy, high quality, strong when they see our brand

5. No preference to color. Maybe more sturdy and corporate. Not fancy.

Industry/Entity Type

CONSTRUCTION SUPPLY

Contact Information for Business Card

Name, Position, office phone mob phone, email

Requirements
Must have
• the company logo
Nice to have
• would like to see a mixture of designs, of with logo only and also with simple graphic designs to bring out the company whilst still have the strong sturdy professional feeling

```html
<!DOCTYPE html>
<html lang="en">
<head>
<meta charset="utf-8">
<title>K T Masonry – Business Card</title>
<link href="https://fonts.googleapis.com/css2?family=Roboto:wght@400;500;700&display=swap" rel="stylesheet">
<style>
  :root {
    --backdrop: #2c2c2c;
    --concrete-light: #ececec;
    --concrete-mid: #d9d9d9;
    --navy: #143d62;
    --navy-deep: #10355a;
    --rim: #3b4048;
    --ink: #1b3f63;
    --ink-soft: #2b4a6b;
    --emboss: #b4b4b4;
    --white: #ffffff;
  }
  * { margin: 0; padding: 0; box-sizing: border-box; }
  html, body {
    width: 1200px; height: 1138px; overflow: hidden;
    background: var(--backdrop);
    font-family: "Roboto", sans-serif;
  }
  .canvas { position: relative; width: 1200px; height: 1138px; }
  .card {
    position: absolute;
    width: 620px; height: 374px;
    border-radius: 14px;
    overflow: hidden;
    background: radial-gradient(ellipse at 40% 35%, var(--concrete-light), var(--concrete-mid));
  }
  .card-front { left: 274px; top: 186px; }
  .card-back { left: 276px; top: 608px; }

  .front-name {
    position: absolute; left: 0; right: 0; top: 152px;
    text-align: center;
    font-size: 42px; font-weight: 500;
    color: var(--emboss);
    letter-spacing: 2px;
  }
  .front-web {
    position: absolute; left: 0; right: 0; top: 330px;
    text-align: center;
    font-size: 15px; font-weight: 500;
    letter-spacing: 7px;
    color: var(--ink);
  }

  .back-shapes { position: absolute; inset: 0; }
  .brand-name {
    position: absolute; left: 22px; width: 260px; top: 208px;
    text-align: center;
    font-size: 30px; font-weight: 500;
    color: var(--white);
    letter-spacing: 1px;
  }
  .contact { position: absolute; left: 348px; top: 66px; color: var(--ink-soft); }
  .person-name { font-size: 22px; font-weight: 700; color: var(--ink); }
  .person-role { font-size: 16px; margin-top: 4px; }
  .details { list-style: none; margin-top: 28px; }
  .details li { display: flex; align-items: center; height: 25.5px; font-size: 16px; }
  .details svg { width: 14px; height: 14px; margin-left: 6px; margin-right: 12px; fill: var(--ink); }
  .address { margin-top: 8px; font-size: 16px; line-height: 26px; }
  .tagline {
    position: absolute; left: 268px; top: 320px; width: 352px; height: 32px;
    display: flex; align-items: center; padding-left: 8px;
    font-size: 16px; color: var(--white);
  }
</style>
</head>
<body>
<main class="canvas">

  <section class="card card-front">
    <div class="front-name">K T Masonry</div>
    <div class="front-web">www.ktmasonry.com</div>
  </section>

  <section class="card card-back">
    <svg class="back-shapes" viewBox="0 0 620 374" preserveAspectRatio="none">
      <path d="M0 0 H262 Q352 190 264 374 H0 Z" fill="var(--rim)"/>
      <path d="M0 0 H236 Q328 190 236 374 H0 Z" fill="var(--navy)"/>
      <rect x="252" y="320" width="368" height="32" fill="var(--navy-deep)"/>
    </svg>

    <div class="brand-name">K T MASONRY</div>

    <div class="contact">
      <div class="person-name">Peter Hallam</div>
      <div class="person-role">Managing Director</div>
      <ul class="details">
        <li><svg viewBox="0 0 16 16"><path d="M2 6c0-2 2-3 6-3s6 1 6 3l-3 1-1-2H6L5 7 2 6zM4 8h8l1 6H3z"/></svg>000 0000 0000</li>
        <li><svg viewBox="0 0 16 16"><path d="M1 3h14v10H1z M2 4l6 5 6-5" fill="none" stroke="var(--ink)" stroke-width="1.6"/></svg>peter@ktmasonry.com</li>
        <li><svg viewBox="0 0 16 16"><circle cx="8" cy="8" r="6.5" fill="none" stroke="var(--ink)" stroke-width="1.4"/><path d="M1.5 8h13M8 1.5c-3 3-3 10 0 13M8 1.5c3 3 3 10 0 13" fill="none" stroke="var(--ink)" stroke-width="1.2"/></svg>www.ktmasonry.com</li>
      </ul>
      <p class="address">18 Harbour Rd., Point Cruz,<br>Honiara, SB 00123</p>
    </div>

    <div class="tagline">Efficient, Professional, Dependable, Reliable</div>
  </section>

</main>
</body>
</html>
```